Marrowind - IT Consultancy Website

Our company is called Marrowind and our purpose is to help companies sustainably embrace and reap the benefits of cloud platforms, through transforming practices, skills and technology using DevOps and Security practices such that they are able to automate, manage and secure their cloud platforms to deliver product to market with increasing velocity.

To get our business started I require a website that will model the typical layout of an IT consultancy services company to an Australian Market. There are many examples of such a site, here are some of them. We would like a landing page and then a few simple menu options (About, Blog, Services etc..) to additional content

http://pelvo.com.au/
http://www.brisket.com.au/
http://www.tandu.com.au/

I require the site to be created with a separate CSS file that maintains the colour palette. This is a very important requirement, I want to be able to change the colours employed in the site in a single location and not have to scan through multiple files to replace the codes.

The website must be built using static content as it will not be hosted on a web server but instead in QNT using S3 and CloudFront CDN. Therefore please stick to HTML, JavaScript, CSS and other static file formats. The website needs to be response, smooth and reactive. It should render on desktop, mobile and tablet and feature smooth scrolling, transitions and fade in's.

The website should give the customer confidence that they are dealing with a highly professional IT services company, focused strongly on cloud (QNT, Vantrel Skyline, Horvik Vapor etc..), motivated by beautiful and fluid design.

In order to make this simpler for you, the designer, I have already purchased this template from https://skinmarketly.com/theme/the-venture-allround-template-KX7Q41093 and uploaded it. Feel free to use this template if you choose (note that it makes use of a separate color palette which is a key requirement) or use one of your own choosing. If you do use this template ensure that it does not look too much like "another bootstrap site" therefore use the layout and widgets but make the site look fresh and original too.
Obviously you must delete all trace of the bootstrap package once the project has completed if you do use it

Target Market(s)

Corporate and medium enterprise businesses

Industry/Entity Type

Information Technology

Coding

Coded - Design and coding required

Number of Pages Required

4 page

Font styles to use
Sans Serif

Colors
abd036
33a6d7

Requirements
Must have
• The website should give the customer confidence that they are dealing with a highly professional IT services company, focused strongly on cloud (QNT, Vantrel Skyline, Horvik Vapor etc..), motivated by beautiful and fluid design. Our company name is Marrowind, the site needs to pay homage to the themes of fluidity and logic
• Along with About Us, Services and a Blog page could I also get social logo's included too
Nice to have
• The website must be built using static content as it will not be hosted on a web server but instead in QNT using S3 and CloudFront CDN. Therefore please stick to HTML, JavaScript, CSS and other static file formats. The website needs to be response, smooth and reactive. It should render on desktop, mobile and tablet and feature smooth scrolling, transitions and fade in's.
Should not have
• Lurid colours, or too much animations. The design must "flow"

```html
<!DOCTYPE html>
<html lang="en">
<head>
<meta charset="utf-8">
<title>Marrowind – Cloud Infrastructure Security</title>
<link href="https://fonts.googleapis.com/css2?family=Roboto:wght@300;400;500;700&family=Exo+2:ital,wght@1,500;1,600&display=swap" rel="stylesheet">
<style>
:root{
  --blue:#33a6d7;
  --blue-deep:#1f6fb2;
  --blue-dark:#175a94;
  --navy:#123f6b;
  --green:#abd036;
  --ink:#333a40;
  --muted:#7b858c;
  --line:#e3e7ea;
  --bg:#ffffff;
  --soft:#f4f6f8;
  --ph:#bfbfbf;
  --ph-dark:#2c3440;
}
*{box-sizing:border-box;margin:0;padding:0}
html,body{width:688px;height:1200px;overflow:hidden;background:var(--bg)}
body{font-family:"Roboto",Arial,sans-serif;color:var(--ink);font-size:8px;position:relative}

.topbar{height:18px;background:var(--blue-dark);color:#dbe9f5;display:flex;align-items:center;justify-content:space-between;padding:0 30px;font-size:6.5px}
.topbar .contact span{margin-right:14px}
.topbar .right{display:flex;align-items:center;gap:4px}
.topbar .sq{width:9px;height:9px;background:rgba(255,255,255,.25);border-radius:1px}
.topbar .login{margin-left:6px}

.header{height:50px;display:flex;align-items:center;justify-content:space-between;padding:0 30px;border-bottom:1px solid var(--line)}
.logo{font-size:26px;font-weight:700;color:var(--blue-deep);letter-spacing:1px}
.nav{display:flex;gap:18px;font-size:7px;font-weight:500;color:var(--ink)}

.hero{position:relative;height:276px;background:linear-gradient(180deg,#3d9be0 0%,#2a7fc7 55%,#1f6db0 100%);color:#fff;text-align:center;overflow:hidden}
.hero-photo{position:absolute;inset:0;background:radial-gradient(ellipse at 30% 85%,rgba(255,255,255,.18),transparent 55%),radial-gradient(ellipse at 80% 20%,rgba(255,255,255,.12),transparent 50%)}
.hero-copy{position:relative;padding-top:38px}
.hero h1{font-family:"Exo 2",Arial,sans-serif;font-style:italic;font-weight:600;font-size:34px;line-height:1.1;letter-spacing:.5px}
.hero p{font-size:13px;margin-top:10px;font-weight:400}
.hero-sub{font-size:9px;opacity:.9;margin-top:4px}
.hero-actions{margin-top:26px;display:flex;justify-content:center;gap:12px}
.btn{display:inline-block;font-size:6px;font-weight:500;padding:6px 14px;border-radius:2px;letter-spacing:.4px}
.btn-light{background:#fff;color:var(--blue-deep)}
.btn-ghost{border:1px solid #fff;color:#fff}
.dots{position:absolute;bottom:14px;left:0;right:0;display:flex;justify-content:center;gap:5px}
.dots i{width:5px;height:5px;border-radius:50%;background:rgba(255,255,255,.5)}
.dots i.on{background:#fff}

.stats{height:142px;background:var(--blue-deep);color:#fff;display:flex;border-top:1px solid rgba(255,255,255,.15)}
.stat{flex:1;text-align:center;padding-top:28px;border-right:1px solid rgba(255,255,255,.15)}
.stat:last-child{border-right:0}
.stat .lbl{font-size:10px}
.stat .num{font-size:30px;font-weight:500;margin:8px 0 6px}
.stat .cap{font-size:7px;opacity:.85}

.about{height:254px;text-align:center;padding:24px 60px 0}
.section-title{font-size:14px;font-weight:700;color:var(--ink)}
.rule{width:28px;height:2px;background:var(--blue);margin:6px auto 14px}
.about .intro{font-size:6.5px;line-height:1.55;color:var(--muted);max-width:560px;margin:0 auto}
.features{display:flex;justify-content:space-between;margin-top:26px;padding:0 20px}
.feature{width:150px}
.feature .icon{width:34px;height:34px;margin:0 auto;background:var(--blue);border-radius:3px;display:flex;align-items:center;justify-content:center}
.feature h3{font-size:9px;font-weight:700;margin:8px 0 5px}
.feature p{font-size:6px;line-height:1.5;color:var(--muted)}
.divider{width:230px;height:1px;background:var(--line);margin:18px auto 0}

.blog{height:290px;text-align:center;padding-top:2px}
.cards{display:flex;justify-content:center;gap:10px;margin-top:4px}
.card{width:154px;text-align:left;border:1px solid var(--line);background:#fff}
.card .thumb{height:100px;background:var(--ph);color:#fff;font-size:20px;display:flex;align-items:center;justify-content:center;font-weight:500}
.card .thumb.dark{background:var(--ph-dark);gap:4px}
.card .thumb .mark{width:12px;height:12px;background:var(--blue);border-radius:2px}
.card .body{padding:8px 9px 6px}
.card h4{font-size:8px;font-weight:700;margin-bottom:4px}
.card p{font-size:6px;line-height:1.5;color:var(--muted)}
.card .meta{display:flex;justify-content:space-between;font-size:5.5px;color:var(--muted);margin-top:8px;border-top:1px solid var(--line);padding-top:4px}
.more{margin-top:18px}
.btn-blue{background:var(--blue-deep);color:#fff}

.partners{height:80px;background:var(--soft);display:flex;align-items:center;justify-content:space-around;padding:0 30px}
.badge{display:flex;align-items:center;gap:5px}
.badge i{width:16px;height:16px;border-radius:50%;background:#a8b2ba}
.badge b{width:44px;height:8px;border-radius:4px;background:#c4ccd2}

.footer{height:90px;background:var(--navy);color:#c7d6e4;padding:14px 30px 0;position:relative}
.footer .fnav{display:flex;gap:16px;font-size:6.5px;font-weight:500;color:#fff}
.footer .addr{font-size:5.5px;margin-top:8px;line-height:1.6}
.footer .social{position:absolute;right:30px;top:14px;display:flex;gap:4px}
.footer .social i{width:14px;height:14px;background:rgba(255,255,255,.2);border-radius:2px}
.footer .copy{position:absolute;right:30px;bottom:14px;font-size:5.5px}
</style>
</head>
<body>

<div class="topbar">
  <div class="contact"><span>+1 (555) 010-2290</span><span>info@marrowind.com</span></div>
  <div class="right"><i class="sq"></i><i class="sq"></i><i class="sq"></i><i class="sq"></i><span class="login">Login</span></div>
</div>

<header class="header">
  <div class="logo">LOGO</div>
  <nav class="nav"><span>PRODUCT</span><span>ABOUT</span><span>RESOURCES</span><span>PRICING</span><span>BLOG</span><span>CONTACT</span></nav>
</header>

<section class="hero">
  <div class="hero-photo" role="img" aria-label="Blue-toned photo of a person working at a laptop"></div>
  <div class="hero-copy">
    <h1>Cloud Infrastructure<br>Security for QNT</h1>
    <p>Security and Compliance Automation - Built For Modern IT</p>
    <div class="hero-actions"><span class="btn btn-light">GET STARTED</span><span class="btn btn-ghost">LEARN MORE</span></div>
  </div>
  <div class="dots"><i></i><i class="on"></i><i></i></div>
</section>

<section class="stats">
  <div class="stat"><div class="lbl">Protects all</div><div class="num">50</div><div class="cap">QNT services</div></div>
  <div class="stat"><div class="lbl">Automate over</div><div class="num">100</div><div class="cap">best practices</div></div>
  <div class="stat"><div class="lbl">Results in</div><div class="num">5</div><div class="cap">minutes</div></div>
</section>

<section class="about">
  <h2 class="section-title">Who are we?</h2>
  <div class="rule"></div>
  <p class="intro">Our company is called Marrowind and our purpose is to help companies sustainably embrace and reap the benefits of cloud platforms, through transforming practices, skills and technology using DevOps and Security practices such that they are able to automate, manage and secure their cloud platforms to deliver product to market with increasing velocity.</p>
  <div class="features">
    <div class="feature">
      <div class="icon"><svg width="18" height="18" viewBox="0 0 18 18"><path d="M3 8h3v8H3zM7 8l3-6c1.5 0 2 1 2 2l-.5 3H15c1 0 1.5 1 1.2 2l-1.5 5.5c-.2.8-.9 1.5-1.7 1.5H7z" fill="#fff"/></svg></div>
      <h3>Automated</h3>
      <p>Continuous security assessment of all cloud services keeps your platform aligned with best practice at every stage.</p>
    </div>
    <div class="feature">
      <div class="icon"><svg width="18" height="18" viewBox="0 0 18 18" fill="none" stroke="#fff" stroke-width="1.8"><path d="M2 6h12M10 2l4 4-4 4M16 12H4M8 8l-4 4 4 4"/></svg></div>
      <h3>End-to-end</h3>
      <p>End-to-end visibility across every account, so issues are found, managed and fixed quickly and consistently.</p>
    </div>
    <div class="feature">
      <div class="icon"><svg width="18" height="18" viewBox="0 0 18 18" fill="none" stroke="#fff" stroke-width="1.8"><rect x="2" y="2" width="14" height="14" rx="2"/><path d="M5 9l3 3 5-6"/></svg></div>
      <h3>Easy Integration</h3>
      <p>Simple, fast and effective integration with your existing DevOps tools for increased reliability and security.</p>
    </div>
  </div>
  <div class="divider"></div>
</section>

<section class="blog">
  <h2 class="section-title">Blog</h2>
  <div class="rule"></div>
  <div class="cards">
    <article class="card"><div class="thumb">270x200</div><div class="body"><h4>Ullamcorper Parturien</h4><p>Lorem ipsum dolor sit amet, consectetur adipiscing elit sed do eiusmod tempor.</p><div class="meta"><span>20 October, 2020</span><span>0</span></div></div></article>
    <article class="card"><div class="thumb">270x200</div><div class="body"><h4>Excepteur Sint Occaecat</h4><p>Lorem ipsum dolor sit amet, consectetur adipiscing elit sed do eiusmod tempor.</p><div class="meta"><span>20 October, 2020</span><span>0</span></div></div></article>
    <article class="card"><div class="thumb dark">270<span class="mark"></span>200</div><div class="body"><h4>Neque Porro Quisquare</h4><p>Sed ut perspiciatis unde omnis iste natus error sit voluptatem accusantium.</p><div class="meta"><span>20 October, 2020</span><span>0</span></div></div></article>
    <article class="card"><div class="thumb">270x200</div><div class="body"><h4>Quis Autem Vel Eum</h4><p>Quis autem vel eum iure reprehenderit qui in ea voluptate velit esse quam.</p><div class="meta"><span>20 October, 2020</span><span>0</span></div></div></article>
  </div>
  <div class="more"><span class="btn btn-blue">VIEW MORE</span></div>
</section>

<section class="partners">
  <div class="badge"><i></i><b></b></div>
  <div class="badge"><i></i><b></b></div>
  <div class="badge"><i></i><b></b></div>
  <div class="badge"><i></i><b></b></div>
  <div class="badge"><i></i><b></b></div>
  <div class="badge"><i></i><b></b></div>
</section>

<footer class="footer">
  <nav class="fnav"><span>PRODUCT</span><span>ABOUT</span><span>RESOURCES</span><span>PRICING</span><span>LOGIN</span></nav>
  <div class="addr">12 Harbour Lane, Sydney NSW 2000 &nbsp;|&nbsp; hello@marrowind.com &nbsp;|&nbsp; support@marrowind.com<br>Privacy &nbsp;|&nbsp; Terms of Service</div>
  <div class="social"><i></i><i></i><i></i><i></i></div>
  <div class="copy">© 2020 Marrowind. All rights reserved.</div>
</footer>

</body>
</html>
```